Corvane Capital Business Cards

These are professional business cards that are for my family office.
Put fake emails and phone numbers as of now until I finalize those components. This family office controls my families investments, assets, and future. The cards should be professional.
..
.
.
.
I just uploaded another variation of a logo I would like to see as a business card to I am inbeteen which logo to use

Target Market(s)

business

Industry/Entity Type

business

Contact Information for Business Card

Professional, wealth related, finance related.

Requirements
Must have
• Logo

```html
<!DOCTYPE html>
<html lang="en">
<head>
<meta charset="utf-8">
<title>Corvane Capital – Business Cards</title>
<link rel="stylesheet" href="https://fonts.googleapis.com/css2?family=Cinzel:wght@500&family=Montserrat:wght@400;600&display=swap">
<style>
  :root {
    --backdrop: #e4e2de;
    --card: #1b2030;
    --card-edge: #151a27;
    --emblem-light: #262d45;
    --emblem-dark: #1f2538;
    --ink-white: #f4f4f6;
    --ink-grey: #a7a9b0;
    --ink-soft: #d9dbe0;
  }
  html, body {
    margin: 0;
    padding: 0;
    width: 900px;
    height: 1200px;
    overflow: hidden;
    background: var(--backdrop);
  }
  .canvas {
    position: relative;
    width: 900px;
    height: 1200px;
  }
  .card {
    position: absolute;
    left: 80px;
    width: 742px;
    height: 442px;
    border-radius: 22px;
    background: var(--card);
    box-shadow: 0 0 0 1px var(--card-edge);
    overflow: hidden;
  }
  .card--front { top: 130px; }
  .card--back  { top: 637px; }

  .emblem {
    position: absolute;
    width: 420px;
    height: 420px;
  }
  .card--front .emblem { left: 430px; top: 8px; }
  .card--back .emblem  { left: 362px; top: 8px; }

  .wordmark {
    position: absolute;
    margin: 0;
    font-family: "Cinzel", serif;
    font-weight: 500;
    font-size: 37px;
    letter-spacing: 0.3px;
    line-height: 1;
    color: var(--ink-white);
    white-space: nowrap;
  }
  .card--front .wordmark { left: 37px; top: 72px; }
  .card--back .wordmark  { left: 32px; top: 313px; font-size: 36px; }

  .holder {
    position: absolute;
    left: 37px;
    top: 188px;
    font-family: "Montserrat", sans-serif;
  }
  .holder__name {
    margin: 0;
    font-size: 26px;
    font-weight: 600;
    color: var(--ink-grey);
    line-height: 1.2;
  }
  .holder__title {
    margin: 2px 0 0;
    font-size: 16px;
    font-weight: 400;
    color: var(--ink-soft);
  }
  .address {
    position: absolute;
    left: 38px;
    top: 270px;
    margin: 0;
    font-family: "Montserrat", sans-serif;
    font-style: normal;
    font-size: 16px;
    line-height: 21px;
    color: var(--ink-soft);
  }
  .contacts {
    position: absolute;
    left: 37px;
    top: 327px;
    margin: 0;
    padding: 0;
    list-style: none;
    font-family: "Montserrat", sans-serif;
    font-size: 16.5px;
    color: var(--ink-soft);
  }
  .contacts li {
    display: flex;
    align-items: center;
    height: 28.5px;
  }
  .contacts svg {
    width: 15px;
    height: 15px;
    margin-right: 10px;
    fill: var(--ink-grey);
  }
  .back-url {
    position: absolute;
    left: 57px;
    top: 355px;
    margin: 0;
    font-family: "Montserrat", sans-serif;
    font-weight: 600;
    font-size: 19.5px;
    color: var(--ink-grey);
  }
</style>
</head>
<body>
<main class="canvas">

  <section class="card card--front" aria-label="Business card front">
    <svg class="emblem" viewBox="0 0 420 420" role="img" aria-label="Corvane Capital emblem area">
      <defs>
        <radialGradient id="emblem-fill-front" cx="40%" cy="35%" r="70%">
          <stop offset="0" stop-color="var(--emblem-light)"/>
          <stop offset="1" stop-color="var(--emblem-dark)"/>
        </radialGradient>
      </defs>
      <circle cx="210" cy="210" r="205" fill="url(#emblem-fill-front)"/>
    </svg>

    <h1 class="wordmark">Corvane Capital</h1>

    <div class="holder">
      <p class="holder__name">Marcus Ellery</p>
      <p class="holder__title">Owner</p>
    </div>

    <address class="address">
      42 Harbor Point Drive<br>
      Linfield, NJ 07100 USA
    </address>

    <ul class="contacts">
      <li>
        <svg viewBox="0 0 24 24" aria-hidden="true"><path d="M6.6 10.8a15.1 15.1 0 0 0 6.6 6.6l2.2-2.2a1 1 0 0 1 1-.25 11.4 11.4 0 0 0 3.6.57 1 1 0 0 1 1 1V20a1 1 0 0 1-1 1A17 17 0 0 1 3 4a1 1 0 0 1 1-1h3.5a1 1 0 0 1 1 1c0 1.25.2 2.45.57 3.57a1 1 0 0 1-.25 1z"/></svg>
        (555)014-2290
      </li>
      <li>
        <svg viewBox="0 0 24 24" aria-hidden="true"><path d="M2 5h20v14H2z M3.5 6.5 12 12.5l8.5-6V6.5z" fill-rule="evenodd"/></svg>
        info@corvanecapital.com
      </li>
      <li>
        <svg viewBox="0 0 24 24" aria-hidden="true"><path d="M12 2a10 10 0 1 0 0 20 10 10 0 0 0 0-20zm-1 17.9A8 8 0 0 1 4.1 11H7c.1 3.3.9 6.4 4 8.9zM7 9H4.3A8 8 0 0 1 11 4.1C8.3 6 7.2 7.6 7 9zm6 10.9c3.1-2.5 3.9-5.6 4-8.9h2.9a8 8 0 0 1-6.9 8.9zM17 9c-.2-1.4-1.3-3-4-4.9A8 8 0 0 1 19.7 9z"/></svg>
        www.corvanecapital.com
      </li>
    </ul>
  </section>

  <section class="card card--back" aria-label="Business card back">
    <svg class="emblem" viewBox="0 0 420 420" role="img" aria-label="Corvane Capital emblem area">
      <defs>
        <radialGradient id="emblem-fill-back" cx="40%" cy="35%" r="70%">
          <stop offset="0" stop-color="var(--emblem-light)"/>
          <stop offset="1" stop-color="var(--emblem-dark)"/>
        </radialGradient>
      </defs>
      <circle cx="210" cy="210" r="205" fill="url(#emblem-fill-back)"/>
    </svg>

    <h2 class="wordmark">Corvane Capital</h2>
    <p class="back-url">www.corvanecapital.com</p>
  </section>

</main>
</body>
</html>
```